Flat bootstrap design for existing site

I'm looking for a modern flat design based around an existing logo. This has to be a custom design (no external templates), and implemented into a bootstrap framework.

The logo is attached as 2 versions - choose whichever you want, that flows better with whatever design you choose.

Added screenshots of the existing site (currently using the default bootstrap layouts). Please make your designs around those pages in the screenshots (i.e. the homepage only has the postal code input and the header). The active page has 3 screenshots, because I wanted to illustrate the other states that would be visible (in the table rows).

This is a moving/junk removal website, just for some context.

Here's some example websites (flat designs) that I like, just to give you an idea of what I'm after.

https://www.plimvora.com/
https://dacklow.com/
https://trevanu.com/
https://quobrintal.com/en/

Coding

Coded - Design and coding required

Number of Pages Required

5+ page

Colors

Designer to choose colors to be used in the design.

Requirements
Must have
• It must be a modern/simple flat design, that is built around the existing logo (attached).
• It has to be implemented using bootstrap.

```html
<!DOCTYPE html>
<html lang="en">
<head>
<meta charset="utf-8">
<title>Haulvane – Booking Details</title>
<link href="https://fonts.googleapis.com/css2?family=Raleway:wght@500;600;700;800&family=Open+Sans:wght@400;600;700&display=swap" rel="stylesheet">
<style>
:root{
  --brand:#4dc9f6;
  --ink:#2e2e2e;
  --muted:#5a5a5a;
  --page:#eef6fa;
  --white:#ffffff;
  --line:#9aa4a8;
  --table-head:#6fbcdb;
  --notice:#d4ecf5;
  --stripe:#e2eff5;
  --accepted:#6fae55;
  --sent:#6fbcdb;
  --pending:#7a878d;
}
*{box-sizing:border-box;margin:0;padding:0}
html,body{width:1200px;height:1085px;overflow:hidden}
body{background:var(--page);font-family:'Open Sans',sans-serif;color:var(--ink);position:relative}
.site-header{position:absolute;left:0;top:0;width:1200px;height:81px;background:var(--white);box-shadow:0 1px 3px rgba(0,0,0,.12)}
.brand{position:absolute;left:99px;top:22px;display:flex;align-items:center;gap:8px;font-family:'Raleway',sans-serif;font-weight:800;font-size:30px;color:var(--brand)}
.brand-dot{width:26px;height:26px;border-radius:50%;background:var(--brand)}
.nav{position:absolute;top:24px;height:34px;display:flex;align-items:center;font-family:'Raleway',sans-serif;font-weight:600;font-size:16px;color:var(--ink)}
.nav-book{left:549px}.nav-how{left:633px}.nav-email{right:99px}
.nav-driver{left:770px;width:148px;justify-content:center;background:var(--brand);color:var(--white)}
.card{position:absolute;left:99px;top:151px;width:1002px;height:363px;background:var(--white);border-top:4px solid var(--brand);box-shadow:0 0 3px rgba(0,0,0,.06)}
.section-title{position:absolute;left:0;width:100%;text-align:center;font-family:'Raleway',sans-serif;font-weight:500;font-size:29px;color:var(--ink)}
.section-title b{font-weight:800}
.card .section-title{top:42px}
.field-label{position:absolute;font-size:13px;color:var(--muted)}
.field{position:absolute;height:35px;border:1px solid var(--line);font-size:12px;color:#777;padding:0 13px;display:flex;align-items:center}
.field-addon{position:absolute;right:0;top:0;width:36px;height:100%;border-left:1px solid var(--line);display:flex;align-items:center;justify-content:center}
.btn-update{position:absolute;left:56px;top:280px;width:103px;height:41px;border-radius:21px;background:var(--brand);color:var(--white);font-weight:700;font-size:15px;display:flex;align-items:center;justify-content:center;letter-spacing:.5px}
.drivers-title{top:572px}
.drivers{position:absolute;left:99px;top:644px;width:1002px;border:1px solid var(--line);background:var(--white)}
.notice{height:48px;background:var(--notice);font-size:16px;padding:12px 0 0 36px;color:#333;font-weight:600}
.drivers table{width:100%;border-collapse:collapse;table-layout:fixed}
.drivers th{height:58px;background:var(--table-head);color:var(--white);font-size:15px;font-weight:600;text-align:left;padding-left:29px;font-family:'Open Sans',sans-serif}
.drivers th.split{border-left:1px solid var(--line)}
.drivers td{height:58px;font-size:12px;color:#444;padding-left:29px;border-top:1px solid #c7d0d4;border-left:1px solid var(--line)}
.drivers td:first-child{border-left:none}
.drivers tr.alt td{background:var(--stripe)}
.drivers td.status{padding-left:26px}
.badge{display:inline-flex;width:135px;height:34px;align-items:center;justify-content:center;color:var(--white);font-weight:600;font-size:13px;letter-spacing:.5px}
.badge-accepted{background:var(--accepted)}
.badge-sent{background:var(--sent)}
.badge-pending{background:var(--pending)}
.paid{font-weight:700;font-size:14px;color:#333;padding-left:42px!important}
.footer{position:absolute;top:1028px;left:0;width:1200px;text-align:center;font-size:12px;color:#333}
</style>
</head>
<body>
<header class="site-header">
  <div class="brand"><span class="brand-dot"></span>HAULVANE</div>
  <div class="nav nav-book">Book</div>
  <div class="nav nav-how">How it Works</div>
  <div class="nav nav-driver">Become a Driver</div>
  <div class="nav nav-email">mara@pelvint.com</div>
</header>

<section class="card">
  <h1 class="section-title">BOOKING <b>DETAILS</b></h1>
  <label class="field-label" style="left:56px;top:114px">Package Selected:</label>
  <div class="field" style="left:57px;top:139px;width:427px">Package 1
    <span class="field-addon"><svg width="8" height="12" viewBox="0 0 8 12"><path d="M4 0L8 5H0z M4 12L0 7H8z" fill="#888"/></svg></span>
  </div>
  <label class="field-label" style="left:518px;top:114px">Pick-up time Selected:</label>
  <div class="field" style="left:519px;top:139px;width:427px">July 18 at 4:13 am
    <span class="field-addon"><svg width="13" height="13" viewBox="0 0 13 13"><rect x="0.5" y="1.5" width="12" height="11" fill="none" stroke="#999"/><path d="M0.5 4.5H12.5M4.5 4.5V12.5M8.5 4.5V12.5M0.5 8.5H12.5" stroke="#999"/></svg></span>
  </div>
  <label class="field-label" style="left:56px;top:197px">Description:</label>
  <div class="field" style="left:57px;top:221px;width:889px">1 large stove</div>
  <div class="btn-update">UPDATE</div>
</section>

<h2 class="section-title drivers-title">DRIVERS IN <b>YOUR AREA</b></h2>

<section class="drivers">
  <div class="notice">Please stay on this page and be patient, While we contact the drivers and find you one ASAP.</div>
  <table>
    <colgroup><col style="width:171px"><col style="width:171px"><col style="width:274px"><col style="width:189px"><col></colgroup>
    <tr><th>NAME</th><th>DISTANCE (KM)</th><th>AGREED PICK-UP TIME</th><th class="split"></th><th class="split"></th></tr>
    <tr><td>Corin Vale</td><td>4.04km away</td><td>July 18 at 4:13 am</td><td class="status"><span class="badge badge-accepted">TIME ACCEPTED</span></td><td class="paid">PAYMENT MADE</td></tr>
    <tr class="alt"><td>Dalen Pritch</td><td>5.7km away</td><td>-</td><td class="status"><span class="badge badge-sent">REQUEST SENT</span></td><td></td></tr>
    <tr><td>Osric Lammel</td><td>11.13km away</td><td>-</td><td class="status"><span class="badge badge-sent">REQUEST SENT</span></td><td></td></tr>
    <tr class="alt"><td>Tobin Markley</td><td>11.91km away</td><td>-</td><td class="status"><span class="badge badge-pending">PENDING</span></td><td></td></tr>
  </table>
</section>

<footer class="footer">Copyrights © 2017, Haulvane . All Rights Reserved.</footer>
</body>
</html>
```